Webdesign für Sexualpädagogik
Zielgruppe
- Sexualpädagogik, Beratung und Sexualtherapie
- Vorträge und Seminare für Unternehmen / Institutionen Vorträge Sexualität in der Pflege / im Alter / Grenzen wahrnehmen
- Wechseljahreberatung, Beratung in der Lebensmitte
- ZIelgruppe: Menschen, die sich weiternetwickeln möchten, die Problme mit ihrer Sexualität haben, Paare, Jugendliche
letztes Interview in der Zeitung: https://www.talpost-beispiel.ch/nachrichtenblatt/zeitung/frontal-interview/sexualitaet-hoert-nicht-beim-eintritt-ins-spital-auf/
Aufgabenstellung
- bestehende Internetseite siehe unten: Schrift ist Especial Key von Tauwerk Mitte
- auf dem Briefpapier bisher noch der Fachbuchhandel und Onlinhandel, aber beides nicht mehr
- Bilder zum Thema bereist vorhanden
- für Werbeflyer habe ich die Therapie in dunkelblau gehalten udn in der sexualpädagogik in hellblau
der kramkiste wird aus der website entfernet

```html
<!DOCTYPE html>
<html lang="de">
<head>
<meta charset="utf-8">
<title>Tauwerk Mitte – Lust und Liebe Party's</title>
<link href="https://fonts.googleapis.com/css2?family=Roboto:ital,wght@0,300;0,400;0,500;0,700;1,400;1,500&family=Montserrat:wght@500&display=swap" rel="stylesheet">
<style>
:root{
  --brand:#0a4fad;
  --brand-dark:#1d2f8f;
  --ink:#222;
  --body:#333;
  --muted:#666;
  --panel:#f4f4f4;
  --title-box:#333;
  --white:#fff;
}
*{margin:0;padding:0;box-sizing:border-box}
html,body{width:780px;height:1200px;overflow:hidden;background:var(--white)}
body{position:relative;font-family:'Roboto',sans-serif;color:var(--body)}
.side-band{position:absolute;left:0;top:0;width:43px;height:1200px;background:var(--brand)}
.side-band__name{position:absolute;left:22px;top:155px;transform:translate(-50%,-50%) rotate(-90deg);white-space:nowrap;color:var(--white);font-size:17px;font-weight:300;letter-spacing:2px;text-transform:uppercase}
.masthead{position:absolute;left:220px;top:10px;width:360px;height:80px}
.masthead__mark{position:absolute;left:2px;top:14px;width:40px;height:40px;border-radius:50%;background:var(--brand-dark)}
.masthead__name{position:absolute;left:100px;top:6px;font-size:30px;font-weight:500;color:var(--brand-dark);letter-spacing:1px;white-space:nowrap}
.masthead__tagline{position:absolute;left:110px;top:41px;width:230px;text-align:center;font-size:8.5px;font-style:italic;font-weight:500;color:var(--ink)}
.masthead__tagline em{color:var(--brand)}
.masthead__person{position:absolute;left:110px;top:55px;width:230px;text-align:center;font-size:8.5px;font-style:italic;font-weight:500;color:var(--ink)}
.main-nav{position:absolute;left:97px;top:95px;width:580px;height:29px;background:var(--brand);display:flex;justify-content:space-around;align-items:center;padding:0 25px}
.main-nav a{color:var(--white);text-decoration:none;font-size:8.5px;font-weight:700}
.hero{position:absolute;left:97px;top:124px;width:580px;height:136px;background:linear-gradient(100deg,#c8548a 0%,#9a3fb0 30%,#e27bb4 55%,#d96a8f 75%,#6b3aa0 100%)}
.hero__title{position:absolute;left:97px;top:170px;width:228px;height:37px;background:var(--title-box);color:var(--white);font-size:19px;font-weight:300;padding:7px 0 0 22px;clip-path:polygon(0 0,98% 0,100% 100%,0 100%)}
.photo-frame{position:absolute;left:443px;top:240px;width:214px;height:197px;background:var(--white);border:1px solid #ccc}
.photo-frame__img{position:absolute;left:10px;top:9px;width:194px;height:177px;background:radial-gradient(circle at 50% 50%,#d9b5a0 0%,#8a7e7a 55%,#4c4c50 100%)}
.intro{position:absolute;left:98px;top:283px;width:318px;font-size:8.5px;line-height:16.5px;text-align:justify;color:var(--body)}
.intro p+p{margin-top:12px}
.faq{position:absolute;width:256px}
.faq h2{font-size:11px;font-weight:500;color:var(--brand);line-height:14.5px;margin-bottom:7px}
.faq p{font-size:8.5px;line-height:14.5px;text-align:justify}
.faq p+p{margin-top:14px}
.faq--wide{width:581px}
.testimonial{position:absolute;left:97px;top:948px;width:579px;height:159px;background:var(--panel);border:1px solid #e4e4e4}
.testimonial__arrow{position:absolute;top:80px;width:8px;height:8px;border-left:1.5px solid var(--ink);border-bottom:1.5px solid var(--ink)}
.testimonial__avatar{position:absolute;left:57px;top:34px;width:96px;height:96px;border-radius:50%;background:radial-gradient(circle at 50% 40%,#e7d2c2 0%,#b48e6c 60%,#e9e5e0 100%)}
.testimonial__quote{position:absolute;left:140px;top:36px;font-family:Georgia,serif;font-size:56px;line-height:56px;color:var(--brand);font-weight:700}
.testimonial__stars{position:absolute;left:189px;top:28px}
.testimonial__name{position:absolute;left:190px;top:47px;font-family:'Montserrat',sans-serif;font-size:8.5px;letter-spacing:1.8px;color:#777}
.testimonial__text{position:absolute;left:190px;top:63px;width:355px;font-size:7.5px;line-height:11.3px;color:var(--muted)}
.testimonial__rule{position:absolute;left:190px;top:121px;width:15px;height:2px;background:var(--brand)}
.site-footer{position:absolute;left:95px;top:1107px;width:582px;height:34px;background:var(--brand);display:flex;align-items:center;padding:0 13px;font-size:7.8px;font-weight:500}
.site-footer a{color:var(--white);text-decoration:none;margin-right:15px}
.site-footer .legal{margin-left:auto;margin-right:0}
.social{position:absolute;top:1154px;font-size:8px;font-weight:500;color:var(--brand);display:flex;align-items:center;gap:3px}
.social::before{content:"";width:7px;height:7px;border-radius:50%;background:var(--brand)}
</style>
</head>
<body>
<div class="side-band"><span class="side-band__name">Tauwerk Mitte</span></div>

<header class="masthead">
  <span class="masthead__mark"></span>
  <div class="masthead__name">TAUWERK MITTE</div>
  <p class="masthead__tagline">Fachstelle Fur <em>Sexualpadagogik, Beratung</em> und <em>Therapie</em></p>
  <p class="masthead__person">Mara Lindqvist</p>
</header>

<nav class="main-nav">
  <a href="#">HOME</a><a href="#">ÜBER MICH</a><a href="#">GÄSTEBUCH</a><a href="#">NEWSLETTER</a><a href="#">PREISE</a><a href="#">KONTAKT</a>
</nav>

<div class="hero" role="img" aria-label="Bunte Auswahl erotischer Spielzeuge in Pink, Lila und Rosé"></div>
<h1 class="hero__title">Lust und Liebe Party's*</h1>

<div class="photo-frame"><div class="photo-frame__img" role="img" aria-label="Frau mit schwarzer Spitzenmaske, Finger an den Lippen"></div></div>

<section class="intro">
  <p>With wit and wit, sometimes a bit naughty, I show you and your friends in private get-together, what is there in love, pleasure and erotic toys so everything.</p>
  <p>Whether a party or a performance, whether as a gift or as a present for a birthday party, each time a highlight and always exciting and each time very special. Of course, much may be laughed at and talked about, not everything revolves around * The Toy *. I'll show you what * is * and popular. Every woman can contribute her own storys and tips, ideas and ideas about eroticism, sexuality and partnership. Often, as it is a sheltered frame, interesting conversations arise ... how do we like it best, what should happen, what not, what pleases and with what woman has had good experiences and finally we can * speak * about it, questions and reduce uncertainties.</p>
</section>

<section class="faq" style="left:97px;top:488px">
  <h2>Do you fancy a * lust and love party?</h2>
  <p>Call and make an appointment. As the host of a * Lust und Liebe Party you have the opportunity to choose your own personal toy depending on the turnover of the evening.</p>
</section>
<section class="faq" style="left:97px;top:579px">
  <h2>How expensive is that?</h2>
  <p>The goal of such an evening is not only fun, but also the possibility to talk about and about the hot topic of sexuality - love, lust and frustration.</p>
  <p>I would be happy to show you and your friends also in the department in a comfortable atmosphere.</p>
</section>
<section class="faq" style="left:97px;top:701px">
  <h2>May men also participate?</h2>
  <p>For sure! I am not afraid of men and I or we do not do anything to them. But think carefully about whether men fit into such a women's round and if you can then ask the questions and would like to do as you would in a women's round. This can create jammed situations (on the part of women but also on the part of men) and we do not want them on such an evening, but openness.</p>
</section>

<section class="faq" style="left:422px;top:489px">
  <h2>The principle of pleasure and love Party:</h2>
  <p>You are hostess for your girlfriends, cousins, mothers, aunts, sisters, colleagues, etc - the principle works like the Dosenkreis parties. Here may be tried and tested. It should and can be laughed, smiled and marveled.</p>
</section>
<section class="faq" style="left:422px;top:579px">
  <h2>How many should and can participate?</h2>
  <p>From 6 persons up to max. 10. If there are too many, you dare less and the cozy and intimate atmosphere is no longer guaranteed and is gone.</p>
</section>
<section class="faq" style="left:422px;top:661px">
  <h2>What comes to me as a hostess and what do I have to do, do I have obligations?</h2>
  <p>No, not obligations. Your guests will appreciate it very much if you offer a drink and something to nibble on. You create the framework and the conditions, your friends, colleagues, cousins, mothers, grandmothers and aunts will appreciate it and you will be dakbar for a fun, special and exciting evening. And there is also a voucher of 10% of the sales that you can get from your loved ones, or you can invest in your new toy.</p>
</section>

<section class="faq faq--wide" style="left:97px;top:837px">
  <h2>Who do I invite? Tips for the hostess and the selection of her guests</h2>
  <p>Since the issue of sexuality is resisted by many and many do not want to or can not talk about it, I ask you not to persuade anyone. Sometimes curiosity and interest helps to let go of the fun with the other women and the sheltered atmosphere, and to become freer. Best of all, just tell a little bit about and about such an evening, maybe she will express herself sooner or later interest and curiosity. Maybe she needs a little more time and then asks how it was. Let them decide and maybe make you more curious.</p>
</section>

<section class="testimonial">
  <span class="testimonial__arrow" style="left:22px;transform:rotate(45deg)"></span>
  <span class="testimonial__arrow" style="left:553px;transform:rotate(-135deg)"></span>
  <div class="testimonial__avatar" role="img" aria-label="Porträtfoto einer Kundin"></div>
  <div class="testimonial__quote">“</div>
  <svg class="testimonial__stars" width="56" height="10" viewBox="0 0 56 10" aria-hidden="true">
    <g fill="#0a4fad">
      <polygon id="star" points="4.5,0 5.6,3.3 9,3.3 6.3,5.4 7.3,8.8 4.5,6.7 1.7,8.8 2.7,5.4 0,3.3 3.4,3.3"/>
      <use href="#star" x="11.3"/><use href="#star" x="22.6"/><use href="#star" x="33.9"/><use href="#star" x="45.2"/>
    </g>
  </svg>
  <div class="testimonial__name">JONAS BERWALD</div>
  <p class="testimonial__text">Lorem ipsum dolor sit amet, consectetuer adipiscing elit. Class aptent taciti sociosqu ad litora torquent per conubia nostra, per inceptos hymenaeos. Nulla non arcu lacinia neque faucibus fringilla. Ut enim ad minim veniam, quis nostrud exercitation ullamco laboris nisi ut aliquip ex ea commodo consequat. Nam quis nulla. Ut tempus purus at lorem.</p>
  <span class="testimonial__rule"></span>
</section>

<footer class="site-footer">
  <a href="#">Impressum</a><a href="#">Lageplan</a><a href="#">News</a><a href="#">Nächste Seminare</a><a href="#">Kontakt</a><a href="#">über Mara Lindqvist / Tauwerk Mitte</a>
  <a class="legal" href="#">Datenschutz | Terms &amp; Bedingungen</a>
</footer>

<span class="social" style="left:610px">Vernetzt</span>
<span class="social" style="left:652px">Treffpunkt</span>
</body>
</html>
```